Elevating our current Business Card Design

We want to elevate our current business card with a new design to look like a zenith 300 company. We are a premium lubricant distributor (oil and grease).
We need 2 versions, version 1 is as per the uploaded a copy of our current business card with the English version.
For our Chinese version we need to use the front to be English in English and have the back of the card designed exactly like the front for all info to be in Chinese.
The design template needs to be such that we can amend the template with adding different information for each person's card.
The background colour of the card can be changed- we just need to clearly see all information on the card and logos.
The QJR and Ember steady logos cannot have any colour or display changes- only use the logos attached.
All logos need to be included and all information from the attached current card

```html
<!DOCTYPE html>
<html lang="en">
<head>
<meta charset="UTF-8">
<title>Norvale Business Card</title>
<link href="https://fonts.googleapis.com/css2?family=Montserrat:wght@400;500;700;800&display=swap" rel="stylesheet">
<style>
  :root{
    --brand-red:#e8302a;
    --band-grey:#b3b3b6;
    --ink:#1f1f1f;
    --card:#ffffff;
    --stage:#1c1c1c;
    --badge-green:#163f33;
    --badge-red:#e8302a;
    --badge-grey:#8a8a8a;
  }
  *{margin:0;padding:0;box-sizing:border-box}
  html,body{width:1200px;height:1059px;overflow:hidden;background:var(--stage)}
  body{position:relative;font-family:"Montserrat",sans-serif;color:var(--ink)}

  .card{position:absolute;background:var(--card);border-radius:20px;overflow:hidden}
  .card--front{left:257px;top:87px;width:688px;height:393px}
  .card--back{left:252px;top:546px;width:710px;height:401px}

  .card__band{position:absolute;left:0;bottom:0;width:100%}
  .card--front .card__band{height:19px}
  .card--back .card__band{height:18px}

  .wordmark{position:absolute;display:flex;align-items:center;color:var(--brand-red);font-weight:800;letter-spacing:-1px}
  .wordmark__dot{border-radius:50%;background:#f2b32a;flex:none}
  .card--front .wordmark{left:31px;top:168px;font-size:54px;gap:10px}
  .card--front .wordmark__dot{width:26px;height:26px}
  .card--back .wordmark{left:0;width:100%;justify-content:center;top:86px;font-size:86px;gap:16px}
  .card--back .wordmark__dot{width:40px;height:40px}

  .divider{position:absolute;left:319px;top:76px;width:2px;height:244px;background:var(--brand-red)}

  .person{position:absolute;left:338px;top:76px}
  .person__name{font-size:24px;font-weight:800;color:var(--brand-red);line-height:1.1}
  .person__role{font-size:14px;font-weight:500;margin-top:2px}

  .address{position:absolute;left:338px;top:140px;font-size:15px;line-height:18px}

  .contacts{position:absolute;left:335px;top:194px;list-style:none}
  .contacts__item{display:flex;align-items:center;height:24.5px;font-size:14.5px}
  .contacts__icon{width:20px;height:18px;margin-right:15px;fill:var(--brand-red)}

  .badges{position:absolute;left:0;top:0;width:100%;height:100%}
</style>
</head>
<body>

<section class="card card--front">
  <div class="wordmark"><span class="wordmark__dot"></span>Norvale</div>
  <div class="divider"></div>
  <div class="person">
    <p class="person__name">Mara Vellin</p>
    <p class="person__role">Administraction Executive</p>
  </div>
  <p class="address">48 Freightway Drive<br>Ashbury, WA 6021</p>
  <ul class="contacts">
    <li class="contacts__item">
      <svg class="contacts__icon" viewBox="0 0 20 18"><path d="M1 6c0-3 4-4 9-4s9 1 9 4v2h-4V6H5v2H1z"/><rect x="3" y="8" width="14" height="9" rx="2"/><circle cx="10" cy="12.5" r="2.5" fill="#fff"/></svg>
      1300 472 610
    </li>
    <li class="contacts__item">
      <svg class="contacts__icon" viewBox="0 0 20 18"><rect x="5" y="0" width="10" height="18" rx="2"/><rect x="7" y="2.5" width="6" height="11" fill="#fff"/><circle cx="10" cy="15.5" r="1" fill="#fff"/></svg>
      +16 431 207 964
    </li>
    <li class="contacts__item">
      <svg class="contacts__icon" viewBox="0 0 20 18"><rect x="5" y="0" width="10" height="5"/><rect x="1" y="5" width="18" height="8" rx="2"/><rect x="5" y="10" width="10" height="8" fill="#fff" stroke="#e8302a" stroke-width="2"/></svg>
      +16 8 9275 4410
    </li>
    <li class="contacts__item">
      <svg class="contacts__icon" viewBox="0 0 20 18"><rect x="1" y="3" width="18" height="13" rx="1"/><path d="M2 4l8 6 8-6" fill="none" stroke="#fff" stroke-width="1.6"/></svg>
      mara.vellin@norvaledirect.com
    </li>
    <li class="contacts__item">
      <svg class="contacts__icon" viewBox="0 0 20 18"><circle cx="10" cy="9" r="8.5"/><path d="M1.5 9h17M10 0.5v17" fill="none" stroke="#fff" stroke-width="1.4"/></svg>
      www.norvaledirect.com
    </li>
  </ul>
  <svg class="card__band" viewBox="0 0 688 19" preserveAspectRatio="none">
    <rect width="688" height="19" fill="var(--band-grey)"/>
    <polygon points="0,0 331,0 312,19 0,19" fill="var(--brand-red)"/>
    <polygon points="331,0 336,0 317,19 312,19" fill="#fff"/>
  </svg>
</section>

<section class="card card--back">
  <div class="wordmark"><span class="wordmark__dot"></span>Norvale</div>
  <svg class="badges" viewBox="0 0 710 401">
    <rect role="img" aria-label="Ember steady network member badge" x="24" y="252" width="136" height="99" rx="10" fill="var(--badge-green)"/>
    <rect role="img" aria-label="Norvale and Dravon premium lubricants partner badge" x="174" y="288" width="337" height="49" rx="8" fill="var(--badge-red)"/>
    <circle role="img" aria-label="QJR ISO 45001 system certification badge" cx="601" cy="302" r="60" fill="var(--badge-grey)"/>
  </svg>
  <svg class="card__band" viewBox="0 0 710 18" preserveAspectRatio="none">
    <rect width="710" height="18" fill="var(--band-grey)"/>
    <polygon points="0,0 342,0 324,18 0,18" fill="var(--brand-red)"/>
    <polygon points="342,0 347,0 329,18 324,18" fill="#fff"/>
  </svg>
</section>

</body>
</html>
```